Mobile welding fabrication and repair, heavy equipment and semi repair

We need a business card design that will catch the eye but look prelesional at the same time. Were based out of Idaho and we do all welding fabrication jobs and repairs, we also build and install custom pipe fences for personal or larger scale fence jobs and can give free quotes. We can do semi truck and trailer repairs Mobily also.

Target Market(s)

Welding

Industry/Entity Type

welding and repair

Contact Information for Business Card

email (ravenforgeandmend@mailbay.net, phone number 208-417-3826, owner (Dalton Whitcomb), Pipe Fence, Semi Repair, Mobile welding and fabrication

Font styles to use
Sans Serif

Requirements
Must have
• My logo in black background on one side , and other side my logo in white back round with all the information listed on card details
Nice to have
• make it stand out from other business cards

```html
<!DOCTYPE html>
<html lang="en">
<head>
<meta charset="utf-8">
<title>Raven Forge and Mend – Business Card</title>
<link href="https://fonts.googleapis.com/css2?family=Montserrat:wght@400;500;700;800&display=swap" rel="stylesheet">
<style>
  :root {
    --bg: #c4c4c4;
    --card-white: #ffffff;
    --card-dark: #2d2d2e;
    --blue-deep: #1b3f9c;
    --blue-mid: #1a6fc9;
    --blue-bright: #13a2e0;
    --ink: #222a33;
    --ink-soft: #3b4450;
    --band-text: #ffffff;
  }
  * { box-sizing: border-box; margin: 0; padding: 0; }
  html, body { width: 1200px; height: 788px; overflow: hidden; }
  body {
    background: var(--bg);
    font-family: "Montserrat", Arial, sans-serif;
    display: flex;
    flex-direction: column;
    align-items: center;
    justify-content: center;
    gap: 44px;
  }
  .card {
    position: relative;
    width: 560px;
    height: 320px;
    border-radius: 22px;
    overflow: hidden;
    box-shadow: 0 10px 24px rgba(0,0,0,0.22);
  }

  /* Front side */
  .card--front { background: var(--card-white); }
  .front-brand {
    position: absolute;
    left: 40px;
    top: 96px;
    width: 220px;
    display: flex;
    align-items: center;
    gap: 10px;
  }
  .brand-mark {
    width: 14px; height: 14px;
    background: var(--blue-mid);
    flex: none;
  }
  .brand-name {
    font-weight: 800;
    font-size: 22px;
    line-height: 1.1;
    letter-spacing: 0.02em;
    color: var(--blue-mid);
    text-transform: uppercase;
  }
  .front-divider {
    position: absolute;
    left: 276px;
    top: 64px;
    width: 1px;
    height: 150px;
    background: var(--blue-mid);
  }
  .front-details {
    position: absolute;
    left: 298px;
    top: 60px;
    right: 20px;
  }
  .owner-name {
    font-weight: 800;
    font-size: 21px;
    letter-spacing: 0.03em;
    color: var(--blue-deep);
    text-transform: uppercase;
  }
  .owner-role {
    font-size: 12px;
    color: var(--ink);
    margin-top: 2px;
    margin-bottom: 14px;
  }
  .contact-list { list-style: none; }
  .contact-list li {
    display: flex;
    align-items: center;
    gap: 7px;
    font-size: 11px;
    font-weight: 500;
    color: var(--ink-soft);
    line-height: 1.9;
  }
  .contact-icon { width: 10px; height: 10px; flex: none; fill: var(--blue-deep); }
  .service-band {
    position: absolute;
    left: 0; right: 0; bottom: 0;
    height: 42px;
    background: linear-gradient(90deg, var(--blue-deep) 0%, var(--blue-bright) 55%, var(--blue-deep) 100%);
    display: flex;
    align-items: center;
    justify-content: center;
    color: var(--band-text);
    font-size: 12.5px;
    font-weight: 500;
    letter-spacing: 0.02em;
  }

  /* Back side */
  .card--back { background: var(--card-dark); }
  .back-brand {
    position: absolute;
    right: 34px;
    bottom: 40px;
    display: flex;
    align-items: center;
    gap: 10px;
  }
  .back-brand .brand-name { font-size: 26px; color: var(--blue-bright); }
  .back-brand .brand-mark { background: var(--blue-bright); }
</style>
</head>
<body>

  <section class="card card--front" aria-label="Business card front">
    <div class="front-brand">
      <span class="brand-mark" aria-hidden="true"></span>
      <span class="brand-name">Raven Forge and Mend</span>
    </div>
    <div class="front-divider" aria-hidden="true"></div>
    <div class="front-details">
      <h1 class="owner-name">Dalton Whitcomb</h1>
      <p class="owner-role">Owner</p>
      <ul class="contact-list">
        <li>
          <svg class="contact-icon" viewBox="0 0 10 10" aria-hidden="true"><path d="M2 0.5 L3.6 0.5 L4.3 2.6 L3.2 3.5 Q4.2 5.8 6.5 6.8 L7.4 5.7 L9.5 6.4 L9.5 8 Q9.5 9.5 8 9.5 Q0.5 9 0.5 2 Q0.5 0.5 2 0.5 Z"/></svg>
          208-417-3826
        </li>
        <li>
          <svg class="contact-icon" viewBox="0 0 10 10" aria-hidden="true"><path d="M0.5 2 H9.5 V8.5 H0.5 Z M1 2.4 L5 5.6 L9 2.4" fill="none" stroke="#1b3f9c" stroke-width="1"/></svg>
          ravenforgeandmend@mailbay.net
        </li>
        <li>
          <svg class="contact-icon" viewBox="0 0 10 10" aria-hidden="true"><circle cx="5" cy="5" r="4.3" fill="none" stroke="#1b3f9c" stroke-width="1"/><path d="M0.7 5 H9.3 M5 0.7 Q2.3 5 5 9.3 M5 0.7 Q7.7 5 5 9.3" fill="none" stroke="#1b3f9c" stroke-width="0.8"/></svg>
          www.ravenforgeandmend.ch
        </li>
      </ul>
    </div>
    <div class="service-band">Pipe Fence &nbsp;•&nbsp; Semi Repair &nbsp;•&nbsp; Mobile welding and fabrication</div>
  </section>

  <section class="card card--back" aria-label="Business card back">
    <div class="back-brand">
      <span class="brand-mark" aria-hidden="true"></span>
      <span class="brand-name">Raven Forge and Mend</span>
    </div>
  </section>

</body>
</html>
```